i need a business card for a plumbing company in california

we are a drain cleaning , maintenance plumbing company who is starting new marketing campaign for a tatrench-less pipe installation department .

Target Market(s)

the professional who appreciates time and quality workmanship.

Industry/Entity Type

Plumbing

Colors
0655a3
ec1f27

Requirements
Must have
• the second logo needs to be included
Nice to have
• a focus on the services offered
Should not have
• any underlined words on the brief

```html
<!DOCTYPE html>
<html lang="en">
<head>
<meta charset="utf-8">
<title>Clearline Plumbing – Business Card</title>
<link href="https://fonts.googleapis.com/css2?family=Russo+One&family=Roboto:wght@400;500&family=Roboto+Condensed:wght@700&display=swap" rel="stylesheet">
<style>
  :root {
    --brand-red: #e0262c;
    --brand-red-dark: #c41d22;
    --brand-red-light: #e8393c;
    --steel: #9a9a92;
    --steel-light: #c9c9c2;
    --ink: #7d7d7d;
    --paper: #ffffff;
    --paper-shade: #efefef;
    --backdrop: #e9e6e1;
  }
  * { box-sizing: border-box; margin: 0; padding: 0; }
  html, body { width: 1200px; height: 780px; overflow: hidden; }
  body {
    background: var(--backdrop);
    font-family: "Roboto", Arial, sans-serif;
    position: relative;
  }
  .card {
    position: absolute;
    top: 235px;
    width: 540px;
    height: 309px;
    border-radius: 22px;
    overflow: hidden;
    box-shadow: 0 6px 18px rgba(0,0,0,.18);
  }
  .card--front { left: 40px; background: linear-gradient(160deg, var(--paper), var(--paper-shade)); }
  .card--back  { left: 620px; background: radial-gradient(circle at 40% 30%, var(--brand-red-light), var(--brand-red-dark)); }

  .front-swoosh { position: absolute; inset: 0; width: 100%; height: 100%; }

  .holder { position: absolute; top: 16px; right: 34px; text-align: right; color: var(--paper); }
  .holder__name { font-family: "Roboto Condensed", sans-serif; font-weight: 700; font-size: 19px; letter-spacing: .5px; }
  .holder__role { font-size: 12px; margin-top: 1px; }

  .wordmark {
    position: absolute;
    display: flex; align-items: center; gap: 10px;
    font-family: "Russo One", sans-serif;
    line-height: .95;
  }
  .wordmark__dot { width: 20px; height: 20px; border-radius: 50%; flex: none; }
  .card--front .wordmark { left: 140px; top: 146px; color: var(--ink); font-size: 30px; }
  .card--front .wordmark__dot { background: var(--brand-red); }
  .card--back .wordmark { left: 50%; top: 50%; transform: translate(-50%, -50%); color: var(--paper); font-size: 36px; }
  .card--back .wordmark__dot { background: var(--paper); width: 24px; height: 24px; }

  .address { position: absolute; right: 30px; top: 150px; text-align: right; color: var(--ink); font-size: 12.5px; line-height: 1.45; }

  .rule { position: absolute; left: 40px; right: 30px; top: 236px; height: 1.5px; background: var(--brand-red); }

  .contacts { position: absolute; left: 40px; right: 30px; top: 248px; display: flex; gap: 40px; }
  .contacts__col { display: flex; flex-direction: column; gap: 5px; }
  .contact { display: flex; align-items: center; gap: 7px; font-size: 12px; color: var(--ink); }
  .contact svg { width: 16px; height: 16px; flex: none; }
</style>
</head>
<body>

<section class="card card--front" aria-label="Card front">
  <svg class="front-swoosh" viewBox="0 0 540 309" preserveAspectRatio="none" aria-hidden="true">
    <path d="M0 0 H540 V62 C330 40 110 80 0 250 Z" fill="var(--brand-red)"/>
    <path d="M540 58 C330 36 105 76 -4 246" fill="none" stroke="var(--steel-light)" stroke-width="6"/>
    <path d="M540 70 C335 50 115 90 0 262" fill="none" stroke="var(--steel)" stroke-width="2"/>
  </svg>

  <div class="holder">
    <div class="holder__name">DANA REYES</div>
    <div class="holder__role">Manager</div>
  </div>

  <div class="wordmark">
    <span class="wordmark__dot"></span>
    <span>Clearline<br>Plumbing</span>
  </div>

  <div class="address">
    PO Box 418, Harbor Road<br>
    Oakdale, CA 95361
  </div>

  <div class="rule"></div>

  <div class="contacts">
    <div class="contacts__col">
      <div class="contact">
        <svg viewBox="0 0 16 16" aria-hidden="true"><circle cx="8" cy="8" r="7.5" fill="var(--brand-red)"/><path d="M5 4.5h2l.6 2-1.1.8a5 5 0 0 0 2.2 2.2l.8-1.1 2 .6v2c-3.5.3-6.8-3-6.5-6.5z" fill="#fff"/></svg>
        (555) 410 2286
      </div>
      <div class="contact">
        <svg viewBox="0 0 16 16" aria-hidden="true"><circle cx="8" cy="8" r="7.5" fill="var(--brand-red)"/><rect x="4.5" y="4" width="7" height="8" rx="1" fill="#fff"/><rect x="5.5" y="5" width="5" height="3" fill="var(--brand-red)"/></svg>
        (555) 410 2287
      </div>
    </div>
    <div class="contacts__col">
      <div class="contact">
        <svg viewBox="0 0 16 16" aria-hidden="true"><circle cx="8" cy="8" r="7.5" fill="var(--brand-red)"/><rect x="4" y="5" width="8" height="6" fill="#fff"/><path d="M4 5l4 3.5L12 5" fill="none" stroke="var(--brand-red)" stroke-width="1"/></svg>
        hello@clearlineplumb.com
      </div>
      <div class="contact">
        <svg viewBox="0 0 16 16" aria-hidden="true"><circle cx="8" cy="8" r="7.5" fill="var(--brand-red)"/><circle cx="8" cy="8" r="4" fill="none" stroke="#fff" stroke-width="1"/><path d="M4 8h8M8 4c-2 2.5-2 5.5 0 8M8 4c2 2.5 2 5.5 0 8" fill="none" stroke="#fff" stroke-width=".8"/></svg>
        www.clearlineplumb.com
      </div>
    </div>
  </div>
</section>

<section class="card card--back" aria-label="Card back">
  <div class="wordmark">
    <span class="wordmark__dot"></span>
    <span>Clearline<br>Plumbing</span>
  </div>
</section>

</body>
</html>
```